Update Powerpoint Presentation

We need to update the existing Powerpoint presentation to make it look more professional, less words and get the message across to potential clients. Our clients are banks and lenders in Australia.
Reason: To give the designers more time to come up with designs
Reason: I am looking for a design that is more innovative and doesn't just re-create what I gave. This presentation is only an example of what I would like I am keen to find a presentation that takes it to the next level.
It Professional

```html
<!DOCTYPE html>
<html lang="en">
<head>
<meta charset="utf-8">
<title>Overview – Web Signing</title>
<link href="https://fonts.googleapis.com/css2?family=Carlito:ital,wght@0,400;0,700;1,700&display=swap" rel="stylesheet">
<style>
  :root {
    --navy-deep: #1b3f6b;
    --panel-blue: #2c5685;
    --panel-edge: #4a6f99;
    --tile-fill: rgba(255, 255, 255, 0.08);
    --tile-edge: rgba(255, 255, 255, 0.22);
    --accent: #8fb8e6;
    --footer-blue: #234e7c;
    --ink-white: #ffffff;
    --ink-soft: #dbe6f3;
    --rule-grey: #3a3a3a;
    --brand-blue: #1d4f91;
    --page-bg: #ffffff;
  }
  * { box-sizing: border-box; margin: 0; padding: 0; }
  html, body { width: 1200px; height: 900px; overflow: hidden; background: var(--page-bg); }
  body { font-family: "Carlito", "Calibri", Arial, sans-serif; color: var(--ink-white); }

  .slide { position: relative; width: 1200px; height: 900px; background: var(--page-bg); }

  /* Header */
  .slide-title {
    position: absolute; left: 37px; top: 66px;
    font-size: 26px; font-weight: 700; font-style: italic;
    color: var(--navy-deep); letter-spacing: 0.2px;
  }
  .title-rule {
    position: absolute; left: 172px; top: 89px; width: 866px; height: 1.5px;
    background: var(--rule-grey);
  }
  .brand {
    position: absolute; right: 36px; top: 36px;
    display: flex; align-items: center; gap: 9px;
  }
  .brand-mark { width: 12px; height: 12px; background: var(--brand-blue); }
  .brand-name { font-size: 38px; font-weight: 700; color: var(--brand-blue); line-height: 1; }

  /* Panels */
  .panel {
    position: absolute; left: 41px; width: 1119px;
    background: var(--panel-blue);
    border: 1px solid var(--panel-edge);
  }
  .panel--intro { top: 138px; height: 357px; }
  .panel--how { top: 527px; height: 286px; }

  .panel-shadow {
    position: absolute; left: 70px; width: 1060px; height: 14px;
    background: radial-gradient(ellipse at center top, rgba(60,60,60,0.55) 0%, rgba(120,120,120,0.25) 45%, rgba(255,255,255,0) 75%);
  }
  .panel-shadow--intro { top: 497px; }
  .panel-shadow--how { top: 815px; }

  .panel-label {
    position: absolute; left: 0; top: 0; bottom: 0; width: 270px;
    display: flex; flex-direction: column; align-items: center; justify-content: center; gap: 10px;
    font-size: 24px; font-weight: 700;
    border-right: 1px solid var(--tile-edge);
  }
  .panel-label::after { content: ""; width: 40px; height: 3px; background: var(--accent); }

  .panel-body { position: absolute; left: 310px; right: 28px; }

  /* Introduction */
  .panel--intro .panel-body { top: 38px; }
  .lead {
    font-size: 24px; font-weight: 400; line-height: 1.35; color: var(--ink-white);
  }
  .lead strong { font-weight: 700; }
  .feature-row {
    display: grid; grid-template-columns: repeat(3, 1fr); gap: 20px;
    margin-top: 38px; list-style: none;
  }
  .feature {
    height: 150px; padding: 20px 20px;
    background: var(--tile-fill); border: 1px solid var(--tile-edge);
    border-top: 3px solid var(--accent);
  }
  .feature-icon { display: block; width: 34px; height: 34px; margin-bottom: 14px; }
  .feature-text { font-size: 18px; line-height: 1.3; color: var(--ink-soft); }
  .feature-text strong { color: var(--ink-white); font-weight: 700; }

  /* How it works */
  .panel--how .panel-body { top: 28px; }
  .how-intro { font-size: 19px; color: var(--ink-soft); }
  .step-row {
    display: flex; align-items: center; margin-top: 22px; list-style: none;
  }
  .step {
    flex: 0 0 236px; height: 178px; padding: 18px 18px;
    background: var(--tile-fill); border: 1px solid var(--tile-edge);
  }
  .step-head { display: flex; align-items: center; gap: 12px; margin-bottom: 12px; }
  .step-number {
    width: 34px; height: 34px; border-radius: 50%;
    background: var(--ink-white); color: var(--panel-blue);
    display: flex; align-items: center; justify-content: center;
    font-size: 19px; font-weight: 700;
  }
  .step-title { font-size: 22px; font-weight: 700; }
  .step-text { font-size: 17px; line-height: 1.3; color: var(--ink-soft); }
  .step-arrow { flex: 1 1 auto; display: flex; justify-content: center; }
  .step-arrow svg { width: 28px; height: 20px; }

  /* Footer */
  .footer {
    position: absolute; left: 0; bottom: 0; width: 1200px; height: 41px;
    background: var(--footer-blue);
    display: flex; align-items: center; justify-content: space-between;
    padding: 0 24px 0 32px; font-size: 19px;
  }
  .footer-date { position: absolute; left: 0; right: 0; text-align: center; pointer-events: none; }
</style>
</head>
<body>
<main class="slide">
  <h1 class="slide-title">OVERVIEW</h1>
  <div class="title-rule"></div>

  <div class="brand">
    <span class="brand-mark"></span>
    <span class="brand-name">Norvale</span>
  </div>

  <section class="panel panel--intro">
    <h2 class="panel-label">Introduction</h2>
    <div class="panel-body">
      <p class="lead"><strong>Web Signing</strong> lets Borrowers review and execute loan documents electronically, through an encrypted web site.</p>
      <ul class="feature-row">
        <li class="feature">
          <svg class="feature-icon" viewBox="0 0 34 34" aria-hidden="true"><circle cx="17" cy="17" r="16" fill="none" stroke="#8fb8e6" stroke-width="2"/><path d="M10 17.5l5 5 9-10" fill="none" stroke="#ffffff" stroke-width="2.6" stroke-linecap="round" stroke-linejoin="round"/></svg>
          <p class="feature-text"><strong>An alternative</strong> to mail and office signings</p>
        </li>
        <li class="feature">
          <svg class="feature-icon" viewBox="0 0 34 34" aria-hidden="true"><circle cx="17" cy="17" r="16" fill="none" stroke="#8fb8e6" stroke-width="2"/><path d="M10 17.5l5 5 9-10" fill="none" stroke="#ffffff" stroke-width="2.6" stroke-linecap="round" stroke-linejoin="round"/></svg>
          <p class="feature-text"><strong>Nothing to install</strong> – no special software or equipment</p>
        </li>
        <li class="feature">
          <svg class="feature-icon" viewBox="0 0 34 34" aria-hidden="true"><circle cx="17" cy="17" r="16" fill="none" stroke="#8fb8e6" stroke-width="2"/><path d="M10 17.5l5 5 9-10" fill="none" stroke="#ffffff" stroke-width="2.6" stroke-linecap="round" stroke-linejoin="round"/></svg>
          <p class="feature-text"><strong>Enforceable</strong> – complies with the Electronic Transactions Act</p>
        </li>
      </ul>
    </div>
  </section>
  <div class="panel-shadow panel-shadow--intro"></div>

  <section class="panel panel--how">
    <h2 class="panel-label">How it Works</h2>
    <div class="panel-body">
      <p class="how-intro">An option to enhance the Borrower’s loan experience.</p>
      <ol class="step-row">
        <li class="step">
          <div class="step-head"><span class="step-number">1</span><span class="step-title">Verify</span></div>
          <p class="step-text">Each Borrower’s identity is verified by the lender or a trusted source.</p>
        </li>
        <li class="step-arrow" aria-hidden="true"><svg viewBox="0 0 28 20"><path d="M2 10h20M15 3l8 7-8 7" fill="none" stroke="#8fb8e6" stroke-width="2.6" stroke-linecap="round" stroke-linejoin="round"/></svg></li>
        <li class="step">
          <div class="step-head"><span class="step-number">2</span><span class="step-title">Notify</span></div>
          <p class="step-text">The Borrower is told when the loan documents are ready.</p>
        </li>
        <li class="step-arrow" aria-hidden="true"><svg viewBox="0 0 28 20"><path d="M2 10h20M15 3l8 7-8 7" fill="none" stroke="#8fb8e6" stroke-width="2.6" stroke-linecap="round" stroke-linejoin="round"/></svg></li>
        <li class="step">
          <div class="step-head"><span class="step-number">3</span><span class="step-title">Sign</span></div>
          <p class="step-text">Documents are downloaded, reviewed and approved online.</p>
        </li>
      </ol>
    </div>
  </section>
  <div class="panel-shadow panel-shadow--how"></div>

  <footer class="footer">
    <span class="footer-note">Commercial in Confidence</span>
    <span class="footer-date">June 2013</span>
    <span class="footer-page">Page-11</span>
  </footer>
</main>
</body>
</html>
```